Marwick Law Letterhead

We need a new letterhead design for a Law Firm. The address for the law firm is 1475 Calloway Street, Suite 210, Houston, Texas 77041. Phone Number: 832-361-9027; Fax Number: 832-614-7359. The logo is uploaded to the project.

```html
<!DOCTYPE html>
<html lang="en">
<head>
<meta charset="utf-8">
<title>Marwick Law Letterhead</title>
<link rel="stylesheet" href="https://fonts.googleapis.com/css2?family=Montserrat:wght@400;500;600&display=swap">
<style>
  :root {
    --backdrop: #e9e9eb;
    --paper: #ffffff;
    --crimson-light: #dc1c24;
    --crimson-dark: #6c0010;
    --navy: #223a70;
    --ink: #1c1c1c;
    --signature-tone: #d9d9dc;
  }
  * { box-sizing: border-box; margin: 0; padding: 0; }
  html, body {
    width: 1200px; height: 960px; overflow: hidden;
    background: var(--backdrop);
    font-family: "Montserrat", Arial, sans-serif;
    color: var(--ink);
  }
  .letterhead {
    position: absolute; left: 282px; top: 30px;
    width: 636px; height: 900px;
    background: var(--paper);
    box-shadow: 0 6px 24px rgba(0,0,0,0.12);
    overflow: hidden;
  }
  .header-band { position: absolute; left: 0; top: 0; width: 636px; height: 280px; }
  .contact-block {
    position: absolute; right: 34px; top: 16px;
    color: #fff; font-size: 10px; line-height: 1.35;
    width: 170px;
  }
  .contact-block .address { margin-bottom: 6px; }
  .contact-line { display: flex; align-items: center; gap: 6px; }
  .contact-line svg { width: 10px; height: 10px; fill: #fff; }
  .firm-mark {
    position: absolute; left: 100px; top: 214px;
    display: flex; align-items: center; gap: 10px;
  }
  .firm-mark .mark-dot { width: 30px; height: 30px; border-radius: 50%; background: var(--navy); }
  .firm-mark .firm-name { font-size: 24px; font-weight: 600; color: var(--navy); letter-spacing: 0.5px; }
  .letter-body {
    position: absolute; left: 60px; top: 268px; width: 516px;
    font-size: 10.5px; line-height: 1.5;
  }
  .recipient { font-size: 11px; line-height: 1.45; margin-bottom: 4px; }
  .letter-body p.paragraph { margin-bottom: 12px; }
  .sign-off { font-size: 12px; margin-top: 6px; }
  .signature {
    display: block; width: 120px; height: 34px; margin-top: 6px;
    background: linear-gradient(90deg, var(--signature-tone), #f1f1f3);
    border-radius: 4px;
  }
</style>
</head>
<body>
<main class="letterhead">
  <svg class="header-band" viewBox="0 0 636 280" aria-hidden="true">
    <defs>
      <linearGradient id="crimsonFade" x1="0" y1="0" x2="1" y2="0">
        <stop offset="0" stop-color="var(--crimson-light)"/>
        <stop offset="1" stop-color="var(--crimson-dark)"/>
      </linearGradient>
    </defs>
    <path d="M0 0 H636 V118 C560 150 400 160 280 166 C150 172 50 200 0 250 Z" fill="url(#crimsonFade)"/>
    <path d="M636 130 C560 162 400 172 282 178 C160 184 60 210 16 262" fill="none" stroke="var(--crimson-light)" stroke-width="3"/>
    <path d="M300 188 C190 190 80 214 34 280" fill="none" stroke="var(--navy)" stroke-width="7"/>
  </svg>

  <div class="contact-block">
    <p class="address">1475 Calloway Street,<br>Suite 210, Houston,<br>Texas 77041</p>
    <p class="contact-line">
      <svg viewBox="0 0 24 24"><path d="M6.6 10.8a15 15 0 0 0 6.6 6.6l2.2-2.2c.3-.3.7-.4 1-.2 1.1.4 2.3.6 3.6.6.6 0 1 .4 1 1V20c0 .6-.4 1-1 1A17 17 0 0 1 3 4c0-.6.4-1 1-1h3.5c.6 0 1 .4 1 1 0 1.3.2 2.5.6 3.6.1.3 0 .7-.2 1z"/></svg>
      <span>832-361-9027</span>
    </p>
    <p class="contact-line">
      <svg viewBox="0 0 24 24"><path d="M6 3h12v5H6zM4 9h16a2 2 0 0 1 2 2v6h-4v4H6v-4H2v-6a2 2 0 0 1 2-2zm4 7v3h8v-3z"/></svg>
      <span>832-614-7359</span>
    </p>
  </div>

  <div class="firm-mark">
    <span class="mark-dot"></span>
    <span class="firm-name">Marwick Law</span>
  </div>

  <section class="letter-body">
    <p class="recipient">Mr/s<br>First Name and Last Name<br>Company Name<br>Address</p>
    <p class="paragraph">Lorem ipsum dolor sit amet,consectetur adipiscing sed do eiusmod tempor incididunt laboreet dolore magna aliqua.Ut enim ad minim,veniam, quis nostrud exercitation ullamco laboris nisi ut aliquip exea commodo consequat.Lorem ipsum dolor sit amet,consectetur adipiscing sed do eiusmod tempor incididunt labore et dolore magna aliqua. Ut enim</p>
    <p class="paragraph">Lorem ipsum dolor sit amet, consectetur adipiscing sed do eiusmod tempor incididunt labore et dolore magna aliqua. Ut enim ad minim veniam, quis nostrud exercitation ullamco laboris nisi ut aliquip exea commodo consequat.Duis aute irure dolor in reprehenderit in voluptate velit esse cillum irure dolor in reprehenderit in voluptate velit esse irure</p>
    <p class="paragraph">Lorem ipsum dolor sit amet, consectetur adipiscing sed do eiusmod tempor incididunt labore et dolore magna aliqua. consequat. Duis aute irure dolor in.reprehenderit in voluptate velit esse cillum dolore eu fugiat nulla pariatur. Excepteur sint occaecat cupidatat non proident, sunt in culpa qui officia deserunt mollit,</p>
    <p class="paragraph">Lorem ipsum dolor sit amet, consectetur adipiscing sed do eiusmod tempor incididunt labore et dolore magna aliqua. Ut enim Lorem ipsum dolor sit amet, consectetur adipiscing sed do eiusmod tempor incididunt labore et dolore magna aliqua. Ut enim Lorem ipsum aliqua.ipsum</p>
    <p class="paragraph">Lorem ipsum dolor sit amet, consectetur adipiscing sed do eiusmod tempor incididunt labore et dolore magna aliqua. Ut enim ad minim veniam, quis nostrud exercitation ullamco laboris nisi ut aliquip exea commodo consequat.Duis aute irure dolor in reprehenderit in voluptate velit esse cillum irure dolor in reprehenderit in voluptate velit esse irure</p>
    <p class="paragraph">Lorem ipsum dolor sit amet, consectetur adipiscing sed do eiusmod tempor incididunt labore et dolore magna aliqua. Ut enim ad minim veniam, quis nostrud exercitation ullamco laboris nisi ut aliquip exea commodo consequat.Duis aute irure dolor in reprehenderit in voluptate velit esse cillum irure dolor in reprehenderit in voluptate velit esse irure</p>
    <p class="sign-off">Regards</p>
    <span class="signature" role="img" aria-label="Handwritten signature of Whitfield"></span>
  </section>
</main>
</body>
</html>
```